VANTOL GROUP

This is a company that provides executive protection. Our motto is "New Era in Protection"... I don't want this to look like other security websites. I want it to be clean and sharp and represent a new era. We are based in the bay area so maybe a picture of San Francisco in the background?
I want it to be able to funnel down a couple different categories.
1. About Us
2. Services (Executive Protection, Covert Protection, Residential Protection & Intelligence)
3. Blue Maple (Training & Consulting)
4. Contact Us
I want it to be very clean and modern. I don't want there to be any pictures of bodyguards with ear pieces like every other website.
Target Market(s)
Ultra High Net Worth Individuals
Coding
Coded - Design and coding required
Number of Pages Required
1 page
Requirements
Must have
- Colors of my Symbol
Nice to have
- City in the background, San Francisco, New York or the Pinecrest Lodge in Montana.
Should not have
- Should not look like an KVM website or have photos of bodyguards. I want this to be a clean and simple website with my logo

```html
<!DOCTYPE html>
<html lang="en">
<head>
<meta charset="utf-8">
<title>VANTOL GROUP — New Era in Protection</title>
<link rel="stylesheet" href="https://fonts.googleapis.com/css2?family=Montserrat:wght@500;600;700;800;900&family=Hind:wght@400;500&display=swap">
<style>
:root{
  --crimson:#7a0c12;
  --ink:#1b1b1b;
  --text:#2a2a2a;
  --mist:#f4f0f0;
  --card:#f3f0f0;
  --steel:#bdbdbd;
  --footer:#262626;
  --white:#ffffff;
  --head:"Montserrat",sans-serif;
  --body:"Hind",sans-serif;
}
*{margin:0;padding:0;box-sizing:border-box}
html,body{width:1200px;height:3174px;overflow:hidden}
body{position:relative;background:var(--white);font-family:var(--body);color:var(--text)}
.abs{position:absolute}

/* hero */
.hero-scene{left:0;top:0;width:1200px;height:715px;
  background:
    radial-gradient(ellipse 420px 140px at 780px 420px,rgba(255,190,90,.55),transparent 70%),
    linear-gradient(180deg,#3a1f8a 0%,#6a3aa6 22%,#b24a76 40%,#e07a4a 50%,#3a2c5c 62%,#22204a 80%,#2c2a5a 100%)}
.hero-shape{left:0;top:600px}
.brand{left:132px;top:36px;font-family:var(--head);font-weight:800;font-size:22px;letter-spacing:2px;color:var(--white);display:flex;align-items:center;gap:10px}
.brand-mark{width:18px;height:18px;background:var(--white)}
.nav{top:37px;left:0;width:1200px;height:20px}
.nav a{position:absolute;font-family:var(--head);font-weight:500;font-size:15.5px;color:var(--white);text-decoration:none;letter-spacing:.3px}
.hero-title{left:497px;top:160px;font-family:var(--head);font-weight:900;font-size:64px;line-height:60px;color:var(--white);letter-spacing:.5px}
.dots{left:559px;top:658px;display:flex;gap:10px;align-items:center}
.dots span{width:6px;height:6px;border-radius:50%;background:var(--white)}
.dots .on{width:11px;height:11px;border:2px solid var(--white);background:var(--crimson)}

/* services */
.section-title{font-family:var(--head);font-weight:800;font-size:23px;color:var(--ink);text-align:center;width:1200px;left:0}
.rule{height:3px;background:var(--crimson)}
.card{width:297px;height:352px;top:846px}
.card-bg{position:absolute;left:0;top:0}
.card-icon{position:absolute;left:0;top:38px;width:297px;height:74px;display:flex;justify-content:center;align-items:center}
.card h3{position:absolute;left:0;top:147px;width:297px;text-align:center;font-family:var(--head);font-weight:700;font-size:15px;line-height:19px;color:var(--ink)}
.card p{position:absolute;left:38px;width:221px;text-align:center;font-size:14px;line-height:17px;color:var(--text)}
.btn-outline{position:absolute;left:100px;top:259px;width:98px;height:31px;border:2px solid var(--crimson);font-family:var(--head);font-weight:700;font-size:11.5px;color:var(--crimson);display:flex;align-items:center;justify-content:center}
.card.is-active h3,.card.is-active p{color:var(--white)}
.card.is-active .btn-outline{border-color:var(--white);color:var(--white)}

/* welcome */
.welcome-bg{left:0;top:1265px;width:1200px;height:530px;background:var(--mist)}
.eyebrow{font-family:var(--head);font-weight:600;font-size:16px;color:var(--ink)}
.heading{font-family:var(--head);font-weight:800;color:var(--ink)}
.copy{font-size:18px;line-height:25px;color:var(--text)}
.btn-solid{height:39px;background:var(--crimson);color:var(--white);font-family:var(--head);font-weight:700;font-size:13px;display:flex;align-items:center;justify-content:center}
.emblem{left:739px;top:1334px;width:325px;height:345px;display:flex;align-items:center;justify-content:center;gap:12px}
.emblem-name{font-family:var(--head);font-weight:800;font-size:30px;color:var(--crimson);letter-spacing:1px}
.emblem-mark{width:30px;height:30px;background:var(--crimson)}

/* training */
.training-art{left:143px;top:1800px;width:480px;height:410px;border-radius:50%;
  background:radial-gradient(ellipse at 50% 45%,#4fb8f0 0%,#1f6fb8 22%,#0d3a78 45%,rgba(10,26,51,0) 72%)}
.on-dark{color:var(--white)}

/* consulting */
.divider-v{left:605px;top:2266px;width:1px;height:506px;background:#d6d6d6}
.globe-art{left:543px;top:2335px;width:524px;height:422px;
  background:radial-gradient(circle at 62% 47%,#2a8fb8 0%,#0f4f74 28%,#0a2a44 55%,#061a2c 100%)}

/* footer */
.footer{left:0;top:2816px;width:1200px;height:358px;background:var(--footer)}
.foot-brand{left:132px;top:2950px;display:flex;align-items:center;gap:12px;font-family:var(--head);font-weight:800;font-size:24px;color:var(--white);letter-spacing:1px}
.foot-brand i{width:22px;height:22px;background:var(--white);display:block}
.foot-head{font-family:var(--head);font-weight:700;font-size:13px;color:var(--white);letter-spacing:.3px}
.foot-menu{left:404px;top:2912px;list-style:none}
.foot-menu li{font-family:var(--head);font-size:12px;line-height:20px;color:#d9d9d9}
.foot-row{display:flex;gap:12px;align-items:flex-start}
.foot-row .ico{width:23px;height:23px;border-radius:50%;background:var(--white);flex:none;display:flex;align-items:center;justify-content:center;margin-top:1px}
.foot-row span{font-family:var(--head);font-size:12px;line-height:16px;color:#d9d9d9}
.foot-rule{left:120px;top:3089px;width:932px;height:1px;background:#3c3c3c}
.copyright{left:0;top:3130px;width:1200px;text-align:center;font-family:var(--head);font-size:10.5px;color:#cfcfcf}
</style>
</head>
<body>

<!-- hero -->
<div class="abs hero-scene" role="img" aria-label="San Francisco skyline at dusk with the Bay Bridge lit up over the water"></div>
<svg class="abs hero-shape" width="1200" height="120" viewBox="0 600 1200 120">
  <polygon points="0,628 600,715 1200,628 1200,720 0,720" fill="#ffffff"/>
  <polyline points="0,632 600,712 1200,632" fill="none" stroke="#7a0c12" stroke-width="12"/>
</svg>
<div class="abs brand"><span class="brand-mark"></span>VANTOL GROUP</div>
<nav class="abs nav">
  <a style="left:488px">HOME</a>
  <a style="left:584px">ABOUT US</a>
  <a style="left:717px">SERVICES</a>
  <a style="left:840px">BLUE MAPLE</a>
  <a style="left:968px">CONTACT US</a>
</nav>
<h1 class="abs hero-title">NEW ERA IN<br>PROTECTION</h1>
<div class="abs dots"><span></span><span></span><span class="on"></span><span></span><span></span></div>

<!-- services -->
<h2 class="abs section-title" style="top:767px">OUR SERVICES</h2>
<div class="abs rule" style="left:576px;top:807px;width:49px"></div>

<div class="abs card is-active" style="left:132px">
  <svg class="card-bg" width="297" height="352" viewBox="0 0 297 352">
    <path d="M0 0H297V297L148.5 344L0 297Z" fill="#7a0c12"/>
    <polyline points="0,300 148.5,347 297,300" fill="none" stroke="#bdbdbd" stroke-width="9"/>
  </svg>
  <div class="card-icon">
    <svg width="66" height="60" viewBox="0 0 66 60"><rect x="4" y="16" width="58" height="40" rx="4" fill="none" stroke="#fff" stroke-width="4"/><path d="M23 16V8H43V16" fill="none" stroke="#fff" stroke-width="4"/><line x1="4" y1="32" x2="62" y2="32" stroke="#fff" stroke-width="4"/></svg>
  </div>
  <h3>EXECUTIVE PROTECTION</h3>
  <p style="top:179px">Lorem Ipsum is simply dummy text of the printing and typesetting industry. Lorem Ipsum has.</p>
  <div class="btn-outline">READ MORE</div>
</div>

<div class="abs card" style="left:451px">
  <svg class="card-bg" width="297" height="352" viewBox="0 0 297 352">
    <path d="M0 0H297V297L148.5 344L0 297Z" fill="#f3f0f0"/>
    <polyline points="0,300 148.5,347 297,300" fill="none" stroke="#7a0c12" stroke-width="9"/>
  </svg>
  <div class="card-icon">
    <svg width="70" height="44" viewBox="0 0 70 44"><path d="M3 22C13 8 24 3 35 3S57 8 67 22C57 36 46 41 35 41S13 36 3 22Z" fill="none" stroke="#7a0c12" stroke-width="4"/><circle cx="35" cy="22" r="10" fill="#7a0c12"/></svg>
  </div>
  <h3>COVERT PROTECTION</h3>
  <p style="top:179px">Lorem Ipsum is simply dummy text of the printing and typesetting industry. Lorem Ipsum has.</p>
  <div class="btn-outline">READ MORE</div>
</div>

<div class="abs card" style="left:770px">
  <svg class="card-bg" width="297" height="352" viewBox="0 0 297 352">
    <path d="M0 0H297V297L148.5 344L0 297Z" fill="#f3f0f0"/>
    <polyline points="0,300 148.5,347 297,300" fill="none" stroke="#7a0c12" stroke-width="9"/>
  </svg>
  <div class="card-icon">
    <svg width="64" height="64" viewBox="0 0 64 64"><circle cx="20" cy="32" r="14" fill="none" stroke="#7a0c12" stroke-width="5"/><path d="M34 32H60V42M50 32V40" fill="none" stroke="#7a0c12" stroke-width="5"/></svg>
  </div>
  <h3>RESIDENTIAL PROTECTION<br>&amp; INTELLIGENCE</h3>
  <p style="top:198px">Lorem Ipsum is simply dummy text of the printing.</p>
  <div class="btn-outline">READ MORE</div>
</div>

<!-- welcome -->
<div class="abs welcome-bg"></div>
<div class="abs eyebrow" style="left:132px;top:1322px">WELCOME TO</div>
<h2 class="abs heading" style="left:132px;top:1343px;font-size:31px">VANTOL GROUP</h2>
<div class="abs rule" style="left:132px;top:1386px;width:132px"></div>
<p class="abs copy" style="left:132px;top:1422px;width:480px">There are many variations of passages of Lorem Ipsum available, but the majority have suffered alteration in some form, by injected humour, or randomised words which don't look even slightly believable. If you are going to use a passage of Lorem Ipsum, you need to be sure there isn't anything embarrassing hidden in the middle of text.</p>
<div class="abs btn-solid" style="left:136px;top:1607px;width:120px">READ MORE</div>
<div class="abs emblem"><span class="emblem-mark"></span><span class="emblem-name">VANTOL GROUP</span></div>

<!-- training -->
<svg class="abs" style="left:0;top:1690px" width="1200" height="600" viewBox="0 1690 1200 600">
  <defs>
    <linearGradient id="deep" x1="0" y1="0" x2="0" y2="1">
      <stop offset="0" stop-color="#06112a"/><stop offset=".6" stop-color="#0a1f40"/><stop offset="1" stop-color="#0c2a52"/>
    </linearGradient>
  </defs>
  <polygon points="0,1704 600,1786 1200,1704 1200,2199 600,2279 0,2199" fill="url(#deep)"/>
  <polyline points="0,1706 600,1788 1200,1706" fill="none" stroke="#7a0c12" stroke-width="12"/>
</svg>
<div class="abs training-art" role="img" aria-label="Glowing digital shield with a keyhole above a circuit platform"></div>
<h2 class="abs heading on-dark" style="left:706px;top:1856px;font-size:24px">TRAINING</h2>
<p class="abs copy on-dark" style="left:704px;top:1904px;width:380px;line-height:24px">There are many variations of passages of Lorem Ipsum available, but the majority have suffered alteration in some form, by injected humour, or randomised words which don't look even slightly believable. If you are going to use a passage of Lorem Ipsum, you need to be sure there isn't anything embarrassing .</p>
<div class="abs btn-solid" style="left:706px;top:2103px;width:120px">READ MORE</div>

<!-- consulting -->
<div class="abs divider-v"></div>
<h2 class="abs heading" style="left:132px;top:2386px;font-size:23px">CONSULTING</h2>
<p class="abs copy" style="left:132px;top:2432px;width:358px">There are many variations of passages of Lorem Ipsum available, but the majority have suffered alteration in some form, by injected humour, or randomised words which don't look even slightly believable. If you are going to use a passage of Lorem Ipsum, you need to be sure there isn't anything embarrassing hidden in the middle of text.</p>
<div class="abs btn-solid" style="left:132px;top:2659px;width:119px">READ MORE</div>
<div class="abs globe-art" role="img" aria-label="Glowing network globe with a shield at its centre"></div>

<!-- footer -->
<footer class="abs footer"></footer>
<div class="abs foot-brand"><i></i>VANTOL GROUP</div>

<div class="abs foot-head" style="left:404px;top:2872px">MENU</div>
<ul class="abs foot-menu">
  <li>HOME</li><li>ABOUT US</li><li>SERVICES</li><li>BLUE MAPLE</li><li>CONTACT US</li>
</ul>

<div class="abs foot-head" style="left:639px;top:2872px">CONTACT US</div>
<div class="abs foot-row" style="left:638px;top:2912px">
  <span class="ico"><svg width="10" height="12" viewBox="0 0 10 12"><path d="M5 0C2 0 0 2 0 5C0 8 5 12 5 12S10 8 10 5C10 2 8 0 5 0Z" fill="#262626"/><circle cx="5" cy="4.6" r="1.8" fill="#fff"/></svg></span>
  <span>2150 Harbor Lane<br>Oakland, CA 94607</span>
</div>
<div class="abs foot-row" style="left:638px;top:2964px">
  <span class="ico"><svg width="11" height="11" viewBox="0 0 11 11"><path d="M2 0L4 3L3 4.5C4 6.5 5 7.5 6.5 8L8 7L11 9L9.5 11C4.5 11 0 6.5 0 1.5Z" fill="#262626"/></svg></span>
  <span>Call Us<br>510.555.0142</span>
</div>
<div class="abs foot-row" style="left:638px;top:3014px">
  <span class="ico"><svg width="11" height="8" viewBox="0 0 11 8"><rect width="11" height="8" fill="#262626"/><polyline points="0,0 5.5,4.5 11,0" fill="none" stroke="#fff" stroke-width="1.2"/></svg></span>
  <span>E mail Us<br>info@vantolgroup.com</span>
</div>

<div class="abs foot-head" style="left:947px;top:2872px">FOLLOW US</div>
<div class="abs foot-row" style="left:946px;top:2912px"><span class="ico"></span><span>Like us on<br>CIRCLEBOOK</span></div>
<div class="abs foot-row" style="left:946px;top:2964px"><span class="ico"></span><span>Follow us on<br>CHIRPER</span></div>
<div class="abs foot-row" style="left:946px;top:3014px"><span class="ico"></span><span>Follow us on<br>WORKLINK</span></div>

<div class="abs foot-rule"></div>
<div class="abs copyright">Copyright © 2021 All Rights Reserved</div>

</body>
</html>
```